Design logo, business cards, and web page for new web and bi development consulting company

I've started a Web and Business Intelligence development consulting company. We develop on Quordex's stack, Vistra Studio and Kelda Server. We develop responsive web sites and business intelligence platforms. I plan on focusing on small to medium sized business as my client base. I need a logo, business cards, and a one page web site. We will do more with the web site with you in the next six months if the business survives. The name of the company is Corvalo Integration Solutions, Corvalo for short.

Target Market(s)

small to medium sized businesses

Industry/Entity Type

Business

Contact Information for Business Card

logo
name
title
email
phone

Logo Text

Corvalo Integration Solutions - web and data solutions

Coding

Coded - Design and coding required

Number of Pages Required

1 page

Font styles to use
Sans Serif

Colors
0355a3
0092cd
00a88f
6b449b

Requirements
Nice to have
• web and data solutions

```html
<!DOCTYPE html>
<html lang="en">
<head>
<meta charset="utf-8">
<title>Corvalo Integration Solutions</title>
<link rel="stylesheet" href="https://fonts.googleapis.com/css2?family=Raleway:wght@300;400;500;600&family=Open+Sans:wght@400&family=Dancing+Script:wght@700&display=swap">
<style>
:root{
  --brand-blue:#1a7cc2;
  --brand-deep:#0355a3;
  --ink:#333333;
  --muted:#8a8a8a;
  --soft-bg:#f6f6f6;
  --rule:#e6e6e6;
  --hero-bg:#0b0f16;
  --footer-bg:#2b2b2b;
  --footer-ink:#c8c8c8;
  --white:#ffffff;
}
*{margin:0;padding:0;box-sizing:border-box}
html,body{width:750px;height:1200px;overflow:hidden;background:var(--white)}
body{position:relative;font-family:"Raleway",sans-serif;color:var(--ink)}
.abs{position:absolute}

/* header */
.site-header{left:0;top:0;width:750px;height:62px;background:var(--white);border-top:2px solid var(--brand-blue)}
.brand{left:62px;top:17px;display:flex;align-items:center;gap:7px}
.brand-dot{width:22px;height:22px;border-radius:50%;background:var(--brand-blue)}
.brand-name{font-size:21px;font-weight:300;letter-spacing:1px;color:var(--brand-deep)}
.nav-item{top:0;height:60px;line-height:60px;font-size:8px;font-weight:500;color:var(--ink)}
.nav-item.is-active{background:var(--brand-blue);color:var(--white);width:48px;text-align:center}

/* hero */
.hero{left:0;top:62px;width:750px;height:294px;background:linear-gradient(90deg,#05070a 0%,#0d1520 55%,#0a1422 100%)}
.hero-visual{left:302px;top:10px;width:448px;height:280px;background:radial-gradient(ellipse at 60% 50%,#6d9fd0 0%,#24527f 30%,#0e2238 60%,rgba(10,20,34,0) 80%)}
.hero-arrow{left:30px;top:120px}
.hero-title{left:62px;top:80px;font-size:26px;font-weight:500;color:#2490d6;line-height:1}
.hero-sub{left:62px;top:107px;font-size:22px;font-weight:500;color:#e8e8e8;line-height:1}
.hero-copy{left:62px;top:143px;width:290px;font-size:8.4px;line-height:13px;color:#e6e6e6;font-weight:500}
.btn{display:block;background:var(--brand-blue);color:var(--white);text-align:center;font-family:"Raleway",sans-serif}
.hero-btn{left:62px;top:195px;width:84px;height:27px;line-height:27px;font-size:9px;font-weight:500;box-shadow:0 2px 0 #0f5a92}

/* welcome */
.welcome{left:0;top:356px;width:750px;height:125px;background:var(--soft-bg);border-bottom:1px solid var(--rule);text-align:center}
.welcome-title{left:0;top:23px;width:750px;font-size:16px;font-weight:500;color:var(--ink)}
.welcome-sub{left:0;top:52px;width:750px;font-size:12px;font-weight:400;color:var(--brand-blue)}
.welcome-copy{left:95px;top:75px;width:560px;font-size:9px;line-height:15px;color:#777}

/* services */
.services{left:0;top:481px;width:750px;height:259px;background:var(--soft-bg);border-bottom:1px solid var(--rule)}
.service-card{top:16px;width:149px;height:212px;background:var(--white);box-shadow:0 0 2px rgba(0,0,0,.15)}
.service-media{left:0;top:0;width:149px;height:128px}
.service-title{left:0;top:143px;width:149px;text-align:center;font-size:7.6px;font-weight:600;color:var(--ink)}
.service-copy{left:6px;top:162px;width:137px;text-align:center;font-family:"Open Sans",sans-serif;font-size:6px;line-height:12px;color:#888}

/* feature */
.feature{left:0;top:740px;width:750px;height:234px;background:var(--white)}
.feature-media{left:64px;top:28px;width:184px;height:174px}
.feature-kicker{left:289px;top:37px;font-size:12px;font-weight:500;color:var(--brand-blue)}
.feature-title{left:289px;top:53px;font-size:17px;font-weight:500;color:#444}
.feature-copy{left:290px;top:87px;width:400px;font-family:"Open Sans",sans-serif;font-size:6.6px;line-height:14px;color:#999}
.feature-btn{left:290px;top:173px;width:107px;height:25px;line-height:25px;font-size:8px}

/* testimonials */
.testimonials{left:0;top:974px;width:750px;height:162px;background:var(--soft-bg);border-top:1px solid var(--rule)}
.quote-mark{font-family:"Open Sans",sans-serif;font-size:120px;line-height:1;color:#e1e1e1}
.quote-open{left:70px;top:12px}
.quote-close{left:604px;top:56px}
.testimonials-title{left:0;top:26px;width:750px;text-align:center;font-size:16px;font-weight:500;color:var(--ink)}
.testimonial-text{left:140px;top:62px;width:470px;text-align:center;font-family:"Open Sans",sans-serif;font-size:9.6px;line-height:17px;color:#9a9a9a}
.testimonial-author{left:0;top:111px;width:750px;text-align:center;font-family:"Dancing Script",cursive;font-size:13px;color:#333}

/* footer */
.site-footer{left:0;top:1136px;width:750px;height:64px;background:var(--footer-bg)}
.footer-link{top:17px;font-family:"Open Sans",sans-serif;font-size:7.2px;color:var(--footer-ink)}
.footer-legal{left:62px;top:43px;font-family:"Open Sans",sans-serif;font-size:6.6px;color:var(--footer-ink)}
.social-dot{top:22px;width:18px;height:18px;border-radius:50%;background:#777}
</style>
</head>
<body>

<header class="site-header abs">
  <div class="brand abs"><span class="brand-dot"></span><span class="brand-name">CORVALO</span></div>
  <nav>
    <span class="nav-item is-active abs" style="left:294px">HOME</span>
    <span class="nav-item abs" style="left:363px">ABOUT US</span>
    <span class="nav-item abs" style="left:436px">SERVICES</span>
    <span class="nav-item abs" style="left:506px">SOLUTIONS</span>
    <span class="nav-item abs" style="left:584px">BLOG</span>
    <span class="nav-item abs" style="left:639px">CONTACT US</span>
  </nav>
</header>

<section class="hero abs">
  <div class="hero-visual abs" role="img" aria-label="Hand holding a glowing laptop surrounded by a network of connected icons and a world map"></div>
  <svg class="hero-arrow abs" width="12" height="56" viewBox="0 0 12 56"><polyline points="10,2 2,28 10,54" fill="none" stroke="#8a8a8a" stroke-width="1"/></svg>
  <h1 class="hero-title abs">CORVALO</h1>
  <p class="hero-sub abs">INTEGRATION SOLUTIONS</p>
  <p class="hero-copy abs">It is a long established fact that a reader will be distracted by the readable content of a page when looking at its layout. The point of Lorem Ipsum content here', making it look like readable English.</p>
  <a class="btn hero-btn abs">READ MORE</a>
</section>

<section class="welcome abs">
  <h2 class="welcome-title abs">WELCOME TO CORVALO</h2>
  <p class="welcome-sub abs">BUSINESS INTELLIGENCE DEVELOPMENT CONSULTING COMPANY</p>
  <p class="welcome-copy abs">It is a long established fact that a reader will be distracted by the readable content of a page when looking at its layout. The point of using Lorem Ipsum is that it has a more-or-less normal distribution of letters, as opposed</p>
</section>

<section class="services abs">
  <article class="service-card abs" style="left:62px">
    <div class="service-media abs" role="img" aria-label="Businessman viewed from behind facing a board of strategy sketches" style="background:linear-gradient(180deg,#cfcfcf,#5a5a5a 70%,#2e2e2e)"></div>
    <h3 class="service-title abs">DEVELOP ON QUORDEX'S STACK</h3>
    <p class="service-copy abs">Dolor nunc vule putateulr ips dol consem donec semp ertet lacini ate ultricie upien disse comete dolo lectus fgilla.</p>
  </article>
  <article class="service-card abs" style="left:220px">
    <div class="service-media abs" role="img" aria-label="Aisle of server racks in a data centre" style="background:linear-gradient(180deg,#9fd4ee,#3f6f8f 50%,#1c2f40)"></div>
    <h3 class="service-title abs">VISTRA STUDIO AND KELDA SERVER</h3>
    <p class="service-copy abs">Dolor nunc vule putateulr ips dol consem donec semp ertet lacini ate ultricie upien disse comete dolo lectus fgilla.</p>
  </article>
  <article class="service-card abs" style="left:379px">
    <div class="service-media abs" role="img" aria-label="Woman working on a laptop with floating app icons" style="background:linear-gradient(160deg,#f2f2f2,#d8d4d0 60%,#b9a89a)"></div>
    <h3 class="service-title abs">DEVELOP RESPONSIVE WEB SITES</h3>
    <p class="service-copy abs">Dolor nunc vule putateulr ips dol consem donec semp ertet lacini ate ultricie upien disse comete dolo lectus fgilla.</p>
  </article>
  <article class="service-card abs" style="left:538px">
    <div class="service-media abs" role="img" aria-label="Man holding up a glowing light bulb under a stormy sky" style="background:linear-gradient(180deg,#7f95a8,#4c5d6b 55%,#2a2f33)"></div>
    <h3 class="service-title abs">BUSINESS INTELLIGENCE PLATFORMS</h3>
    <p class="service-copy abs">Dolor nunc vule putateulr ips dol consem donec semp ertet lacini ate ultricie upien disse comete dolo lectus fgilla.</p>
  </article>
</section>

<section class="feature abs">
  <div class="feature-media abs" role="img" aria-label="Desktop computer showing the website home page" style="background:linear-gradient(180deg,#1d2a3a 0%,#2f4a66 55%,#d9d9d9 78%,#f2f2f2 100%)"></div>
  <p class="feature-kicker abs">DEVELOP RESPONSIVE WEB SITES</p>
  <h2 class="feature-title abs">BUSINESS INTELLIGENCE PLATFORMS</h2>
  <p class="feature-copy abs">It is a long established fact that a reader will be distracted by the readable content of a page when looking at its layout. The point of using Lorem Ipsum is that it has a more-or-less normal distribution of letters, as opposed to using 'Content here, content here', making it look like readable English. Many desktop publishing packages and web page editors now default model text, and a search for 'lorem ipsum' will uncover many web sites still in their infancyLorem Ipsum is that it has a more-or-less normal distribudefault model text, lorem ipsum' will uncover many web sites still in their infancy.....</p>
  <a class="btn feature-btn abs">Click Here For More Info</a>
</section>

<section class="testimonials abs">
  <span class="quote-mark quote-open abs">&ldquo;</span>
  <span class="quote-mark quote-close abs">&rdquo;</span>
  <h2 class="testimonials-title abs">OUR TESTIMONIALS</h2>
  <p class="testimonial-text abs">It is a long established fact that a reader will be distracted by the readable content of a page when looking<br>Ipsum iswill uncover many web sites still in their infancy</p>
  <p class="testimonial-author abs">John Doe</p>
</section>

<footer class="site-footer abs">
  <span class="footer-link abs" style="left:62px">Home</span>
  <span class="footer-link abs" style="left:114px">About Us</span>
  <span class="footer-link abs" style="left:178px">Services</span>
  <span class="footer-link abs" style="left:239px">Solutions</span>
  <span class="footer-link abs" style="left:302px">Blog</span>
  <span class="footer-link abs" style="left:351px">Contact Us</span>
  <p class="footer-legal abs">© Copy Rights 2015. Corvalo. All rights reserved.</p>
  <span class="social-dot abs" style="left:595px"></span>
  <span class="social-dot abs" style="left:619px"></span>
  <span class="social-dot abs" style="left:645px"></span>
  <span class="social-dot abs" style="left:669px"></span>
</footer>

</body>
</html>
```